Brell Stone Company Business Cards

Front and Back Business Card - logo and text setup - cool design. I need workable photoshop or illustrator files so I can setup each employee card with design that is created
Updates

Hi everyone, thank you for the great entries. Please no more white and blue cards - there are so many already - black and silver only now please. thanks!

Target Market(s)

Construction Industry - Facility Managers

Industry/Entity Type

Construction

Contact Information for Business Card

I really like contemporary simplistic looks - clean neat....not opposed to seeing some black backrounds

Requirements
Must have
• Logo/website address with design on front only - www.brellstone-example.com (logo attached)
• Back:
• Name/Title/Company Address/Phone/email address
Nice to have
• Cool design
Should not have
• Nothing gimmicky like Fire or Water - since we are a Fire Protection company - it has all been done

```html
<!DOCTYPE html>
<html lang="en">
<head>
<meta charset="utf-8">
<title>Brell Stone Company Business Cards</title>
<link href="https://fonts.googleapis.com/css2?family=Poppins:wght@400;500;700&display=swap" rel="stylesheet">
<style>
  :root {
    --stage: #e9e9e9;
    --black: #141516;
    --black-soft: #2a2c2e;
    --silver: #c3c7cc;
    --silver-light: #eef0f2;
    --silver-dark: #8b9096;
    --ink: #2b2d2f;
  }
  * { box-sizing: border-box; margin: 0; padding: 0; }
  html, body {
    width: 1200px; height: 920px; overflow: hidden;
    background: var(--stage);
    font-family: "Poppins", sans-serif;
  }
  .sheet { position: relative; width: 1200px; height: 920px; }
  .card {
    position: absolute; top: 311px;
    width: 536px; height: 298px;
    box-shadow: 0 6px 18px rgba(0,0,0,.22);
    overflow: hidden;
  }
  .card--front { left: 46px; background: var(--black); }
  .card--back { left: 618px; background: var(--silver-light); }

  .wordmark { font-weight: 700; letter-spacing: -1px; line-height: 1; }
  .card--front .wordmark {
    position: absolute; left: 0; right: 0; top: 118px;
    text-align: center; font-size: 54px; color: var(--silver);
  }
  .front-web {
    position: absolute; left: 0; right: 0; top: 250px;
    text-align: center; font-size: 13px; font-weight: 500;
    color: var(--silver-dark); letter-spacing: .5px;
  }

  .card--back .wordmark {
    position: absolute; left: 36px; top: 128px;
    font-size: 37px; color: var(--black);
  }
  .divider {
    position: absolute; left: 276px; top: 72px; height: 168px;
    border-left: 2px dashed var(--silver-dark);
  }
  .details {
    position: absolute; left: 296px; top: 74px; width: 224px; color: var(--ink);
  }
  .details .name {
    font-size: 17px; font-weight: 500; color: var(--black);
    letter-spacing: .5px; margin-bottom: 4px;
  }
  .details .line { font-size: 12px; line-height: 21px; color: var(--black-soft); }
  .details .contacts { margin-top: 6px; }
  .contact {
    display: flex; align-items: center; gap: 9px;
    font-size: 12px; line-height: 20px; white-space: nowrap;
    color: var(--ink);
  }
  .contact svg { width: 11px; height: 11px; flex: none; color: var(--silver-dark); }
</style>
</head>
<body>
<main class="sheet">
  <section class="card card--front" aria-label="Card front">
    <div class="wordmark">brellstone</div>
    <div class="front-web">www.brellstone-example.com</div>
  </section>

  <section class="card card--back" aria-label="Card back">
    <div class="wordmark">brellstone</div>
    <div class="divider"></div>
    <div class="details">
      <div class="name">DANIEL HARWOOD</div>
      <div class="line">Senior Consultant</div>
      <div class="line">48 Meridian Park</div>
      <div class="line">Drive Lakeview, NY 10000</div>
      <div class="contacts">
        <div class="contact">
          <svg viewBox="0 0 12 12" aria-hidden="true"><path fill="currentColor" d="M2.4 0.8 4 2.6 3.3 4.1c.7 1.6 1.9 2.8 3.6 3.6l1.5-.7 1.8 1.6-.8 1.8C5 10 1.6 6.5 1.2 1.6Z"/></svg>
          <span>(555) 014-2231</span>
        </div>
        <div class="contact">
          <svg viewBox="0 0 12 12" aria-hidden="true"><rect x="3" y="1" width="6" height="3" fill="none" stroke="currentColor" stroke-width="1.3"/><rect x="1" y="4" width="10" height="5" rx="1" fill="currentColor"/><rect x="3" y="7.5" width="6" height="3.5" fill="#eef0f2" stroke="currentColor" stroke-width="1.2"/></svg>
          <span>(555) 014-2232</span>
        </div>
        <div class="contact">
          <svg viewBox="0 0 12 12" aria-hidden="true"><rect x="1" y="2.5" width="10" height="7" fill="none" stroke="currentColor" stroke-width="1.3"/><path d="M1.5 3 6 6.6 10.5 3" fill="none" stroke="currentColor" stroke-width="1.2"/></svg>
          <span>info@brellstone-example.com</span>
        </div>
        <div class="contact">
          <svg viewBox="0 0 12 12" aria-hidden="true"><circle cx="6" cy="6" r="5" fill="currentColor"/><path d="M1 6h10M6 1c2 2.5 2 7.5 0 10M6 1c-2 2.5-2 7.5 0 10" fill="none" stroke="#eef0f2" stroke-width=".9"/></svg>
          <span>www.brellstone-example.com</span>
        </div>
      </div>
    </div>
  </section>
</main>
</body>
</html>
```